Harborline Auto LLC

Car Dealer Customer Service
Address: 2874 Cresthaven Road, Shelbyville, TN 37162
web: www.harborlineautoxq.net
email: harborlineautoxq@mailnest.example
Phone: (931) 555-0148
Phone: (629) 555-0173

```html
<!DOCTYPE html>
<html lang="en">
<head>
<meta charset="utf-8">
<title>Harborline Auto LLC — Business Card</title>
<link href="https://fonts.googleapis.com/css2?family=Montserrat:wght@400;800&display=swap" rel="stylesheet">
<style>
  :root {
    --stage: #3b3c3f;
    --front-blue: #1e7caf;
    --back-blue: #2993cf;
    --brand-blue: #1f6fa8;
    --gold: #e9b345;
    --white: #ffffff;
  }
  html, body {
    margin: 0;
    padding: 0;
    width: 1200px;
    height: 887px;
    overflow: hidden;
    background: var(--stage);
    font-family: "Montserrat", Arial, sans-serif;
  }
  .stage {
    position: relative;
    width: 1200px;
    height: 887px;
  }
  .card {
    position: absolute;
    top: 283px;
    width: 560px;
    height: 320px;
    border-radius: 22px;
    overflow: hidden;
    box-shadow: 0 14px 30px rgba(0,0,0,0.45);
  }
  .card--front {
    left: 30px;
    background: var(--front-blue);
    display: flex;
    flex-direction: column;
    align-items: center;
    justify-content: center;
    gap: 18px;
  }
  .brand-mark {
    width: 70px;
    height: 70px;
    border-radius: 50%;
    background: var(--white);
  }
  .brand-name {
    margin: 0;
    font-weight: 800;
    font-size: 34px;
    letter-spacing: 1px;
    color: var(--white);
    text-transform: uppercase;
    white-space: nowrap;
  }
  .card--back {
    left: 610px;
    background: var(--back-blue);
  }
  .card-swoosh {
    position: absolute;
    inset: 0;
  }
  .back-brand {
    position: absolute;
    left: 338px;
    top: 78px;
    width: 212px;
    display: flex;
    flex-direction: column;
    align-items: center;
    gap: 12px;
  }
  .back-brand .brand-mark {
    width: 54px;
    height: 54px;
    background: var(--brand-blue);
  }
  .back-brand .brand-name {
    font-size: 19px;
    letter-spacing: 0.5px;
    color: var(--brand-blue);
  }
  .contact {
    position: absolute;
    left: 34px;
    top: 96px;
    color: var(--white);
    font-size: 13px;
    line-height: 1.45;
  }
  .contact p { margin: 0; }
  .contact .address { margin-bottom: 8px; }
  .contact-list {
    list-style: none;
    margin: 0;
    padding: 0;
  }
  .contact-list li {
    display: flex;
    align-items: center;
    gap: 8px;
    height: 21px;
  }
  .contact-icon {
    width: 13px;
    height: 13px;
    flex: none;
  }
</style>
</head>
<body>
<main class="stage">

  <section class="card card--front" aria-label="Card front">
    <span class="brand-mark" aria-hidden="true"></span>
    <h1 class="brand-name">Harborline Auto</h1>
  </section>

  <section class="card card--back" aria-label="Card back">
    <svg class="card-swoosh" viewBox="0 0 560 320" width="560" height="320" aria-hidden="true">
      <path d="M176,0 C184,80 222,126 272,156 C352,202 414,250 392,320 L560,320 L560,0 Z" fill="var(--white)"/>
      <path d="M183,0 C191,80 229,124 279,154 C359,200 421,250 400,320 L560,320 L560,0 Z" fill="var(--gold)"/>
      <path d="M198,0 C208,78 250,118 300,148 C380,194 440,246 424,320 L560,320 L560,0 Z" fill="var(--white)"/>
    </svg>

    <div class="back-brand">
      <span class="brand-mark" aria-hidden="true"></span>
      <h2 class="brand-name">Harborline Auto</h2>
    </div>

    <div class="contact">
      <p>Car Dealer Customer Service</p>
      <p class="address">2874 Cresthaven Road,<br>Shelbyville, TN 37162</p>
      <ul class="contact-list">
        <li>
          <svg class="contact-icon" viewBox="0 0 16 16" aria-hidden="true"><path d="M3 1 L6 1 L7 5 L5 6.5 C6 9 7 10 9.5 11 L11 9 L15 10 L15 13 C15 14 14 15 13 15 C6.5 15 1 9.5 1 3 C1 2 2 1 3 1 Z" fill="var(--gold)"/></svg>
          <span>(931) 555-0148</span>
        </li>
        <li>
          <svg class="contact-icon" viewBox="0 0 16 16" aria-hidden="true"><path d="M1 6 C1 3 15 3 15 6 L12 7 L11 5 L5 5 L4 7 Z" fill="var(--gold)"/><rect x="3" y="8" width="10" height="6" rx="1" fill="var(--gold)"/></svg>
          <span>(629) 555-0173</span>
        </li>
        <li>
          <svg class="contact-icon" viewBox="0 0 16 16" aria-hidden="true"><rect x="1" y="3" width="14" height="10" fill="var(--gold)"/><path d="M1 3 L8 9 L15 3" fill="none" stroke="var(--back-blue)" stroke-width="1.3"/></svg>
          <span>harborlineautoxq@mailnest.example</span>
        </li>
        <li>
          <svg class="contact-icon" viewBox="0 0 16 16" aria-hidden="true"><circle cx="8" cy="8" r="7" fill="var(--gold)"/><path d="M1 8 H15 M8 1 C4 5 4 11 8 15 M8 1 C12 5 12 11 8 15" fill="none" stroke="var(--back-blue)" stroke-width="1"/></svg>
          <span>www.harborlineautoxq.net</span>
        </li>
      </ul>
    </div>
  </section>

</main>
</body>
</html>
```